Property Services Company Needs a Brochure Design

Looking for a new brochure design for an existing property services company.

We provide a range of property services from, market research, real estate brokerage, valuation and appraisal, property development and other real estate consulting services.

We would like a fresh modern brochure design with good graphics and features. Our colours are white, blue and orange.

The design should communicate, attention to detail, superior service delivery and distinction in results.
Updates

I would like the brochure to be roughly about 20 pages.

Containing the following,

1) An introduction
2) Contents Page
2) What we do
3) Our Services
4) Agency & Brokerage
5) Real Estate Consulting
6) Market Research
7) Appraisal & Valuation
8) Project Management
9) Property Development

I would also like icons to represent items 4,5,6,7,8 & 9, they should be represented vertically on each of the pages from the contents page and highlighted individually on the pages that they represent.. i.e. on appraisal & valuation page, all six icons will be arranged vertically and the appraisal and valuations icon will be highlighted.

I will also like to have images that depict the services on the various pages.

I have some pages I think will flow which I will upload shortly.

Industry/Entity Type

Real Estate

Font styles to use
Serif

Colors
f78f20
0455a3

```html
<!DOCTYPE html>
<html lang="en">
<head>
<meta charset="utf-8">
<title>Halvern Property Services – Brochure Cover Spread</title>
<link rel="stylesheet" href="https://fonts.googleapis.com/css2?family=Tinos:wght@400;700&family=Arimo:wght@400&display=swap">
<style>
  :root {
    --navy: #2a2562;
    --orange: #e05f0f;
    --panel-grey: #dadada;
    --ink: #1f1f1f;
    --paper: #ffffff;
    --frame: #9a9a9a;
    --serif: "Tinos", "Times New Roman", serif;
    --sans: "Arimo", Arial, sans-serif;
  }
  * { box-sizing: border-box; margin: 0; padding: 0; }
  html, body { width: 1200px; height: 864px; overflow: hidden; background: var(--paper); }
  .canvas {
    position: relative; width: 1200px; height: 864px;
    border: 1px solid var(--frame); background: var(--paper);
  }
  .spread {
    position: absolute; left: 40px; top: 35px; width: 1120px; height: 793px;
    outline: 1px solid #555;
  }
  .page { position: absolute; top: 0; height: 793px; overflow: hidden; }
  .page--inside { left: 0; width: 560px; background: var(--paper); }
  .page--cover { left: 560px; width: 560px; border-left: 1px solid #555; }

  /* Inside page */
  .side-bar { position: absolute; top: 0; height: 563px; }
  .side-bar--navy { left: 0; width: 35px; background: var(--navy); }
  .side-bar--orange { right: 0; width: 45px; background: var(--orange); }

  .copy {
    position: absolute; top: 60px;
    font-family: var(--serif); font-size: 12.4px; line-height: 15.1px; color: var(--ink);
  }
  .copy p { margin-bottom: 6px; }
  .copy--left { left: 56px; width: 178px; }
  .copy--right { left: 258px; width: 236px; top: 62px; }
  .section-title {
    font-family: var(--serif); font-weight: 700; font-size: 13.5px;
    color: var(--navy); letter-spacing: 0.2px; margin-bottom: 3px;
  }
  .brand-word { color: var(--orange); }

  .footer-brand {
    position: absolute; left: 0; width: 520px; top: 600px;
    display: flex; align-items: center; justify-content: center; gap: 10px;
  }
  .brand-mark { width: 30px; height: 30px; background: var(--navy); }
  .brand-name {
    font-family: var(--sans); color: var(--navy); line-height: 1;
  }
  .brand-name .name { display: block; font-size: 36px; }
  .brand-name .tag { display: block; font-size: 13px; margin-top: 3px; padding-left: 26px; }

  .contact {
    position: absolute; left: 0; width: 530px; top: 673px;
    font-family: var(--sans); font-size: 12.6px; line-height: 14.6px; color: #111;
    text-align: center;
  }
  .contact .icon { display: inline-block; vertical-align: -2px; margin-right: 2px; }

  .rule-orange { position: absolute; left: 0; top: 745px; width: 560px; height: 12px; background: var(--orange); }
  .rule-navy { position: absolute; left: 0; top: 765px; width: 560px; height: 28px; background: var(--navy); }

  /* Cover page */
  .cover-top { position: absolute; left: 0; top: 0; width: 560px; height: 303px; background: var(--orange); }
  .cover-brand-panel {
    position: absolute; left: 162px; top: 165px; width: 398px; height: 138px;
    background: var(--panel-grey);
    display: flex; align-items: center; justify-content: center; gap: 12px;
  }
  .cover-brand-panel .brand-mark { width: 34px; height: 34px; }
  .cover-brand-panel .brand-name .name { font-size: 38px; }
  .cover-brand-panel .brand-name .tag { font-size: 13.5px; }
  .cover-photo {
    position: absolute; left: 0; top: 303px; width: 560px; height: 490px;
    background:
      linear-gradient(180deg, #efeae2 0%, #c9b79c 38%, #a48a68 62%, #d6c6ad 100%);
  }
</style>
</head>
<body>
<div class="canvas">
  <div class="spread">

    <section class="page page--inside">
      <div class="side-bar side-bar--navy"></div>
      <div class="side-bar side-bar--orange"></div>

      <div class="copy copy--left">
        <p>corporations, to private developers and investors. Our clients depend on our ability to draw on years of experience in the local market, our professionals know their communities and the property market inside and out, and provide knowledgeable, creative solutions to all their real estate needs.</p>
        <p>The combination of our integrated services allows us to provide a superior end to end solution to our clients, customized to their own requirements.&nbsp; Market research is a core component to our business model, allowing us to make informed decisions based based on research findings.&nbsp; Our brokerage team also benefits from this information, allowing our associates to advise clients on how best to maximise return on their investment on the sale or buy side within a short timeline.</p>
        <p>We pay great attention to detail in consideration of our client requirements, delivering mandates with distinction.</p>
      </div>

      <div class="copy copy--right">
        <h2 class="section-title">INTRODUCTION</h2>
        <p><span class="brand-word">HALVERN</span> was incorporated in 1984 as an interior design and property development company. Over the years we have expanded our service with a foundation based on core strengths, unrivalled local expertise, network and knowledge combined with strategic partnerships.</p>
        <p>Halvern offers a comprehensive range of services on a local, regional, national and international basis to tenants, owners, and investors within the residential and commercial property market.</p>
        <p>Our clients depend on our ability to draw on</p>
        <p>Our clients depend on our ability to draw on years of experience in the local market, our professionals know their communities and the property market inside and out, and provide knowledgeable, creative solutions to all their real estate needs.</p>
        <p>We currently provide services to corporations, financial institutions, government agencies, public sector entities, developers and investors. Our knowledge, expertise, experience and technological resources allow us to be a superior service provider.</p>
      </div>

      <div class="footer-brand">
        <span class="brand-mark"></span>
        <span class="brand-name"><span class="name">Halvern</span><span class="tag">Property Services</span></span>
      </div>

      <address class="contact" style="font-style:normal">
        <div>
          <svg class="icon" width="11" height="14" viewBox="0 0 11 14" aria-hidden="true"><path d="M5.5 0C2.5 0 0 2.4 0 5.3 0 9 5.5 14 5.5 14S11 9 11 5.3C11 2.4 8.5 0 5.5 0z" fill="var(--orange)"/><circle cx="5.5" cy="5.3" r="2" fill="#fff"/></svg>
          9th floor, CRESTLINE TOWER, 48, Marina Road
        </div>
        <div>Lagos, Nigeria</div>
        <div>
          <svg class="icon" width="11" height="11" viewBox="0 0 11 11" aria-hidden="true"><path d="M2.2 0.5l2 2.3-1.1 1.5c.7 1.5 1.9 2.7 3.4 3.4l1.5-1.1 2.3 2-1.2 1.9C4.6 10.3.7 6.4.3 1.7z" fill="var(--orange)"/></svg>+234 1 5550142
          <svg class="icon" width="12" height="11" viewBox="0 0 12 11" aria-hidden="true"><rect x="2.5" y="0.5" width="7" height="3.5" fill="var(--orange)"/><rect x="0.5" y="4" width="11" height="5" rx="1" fill="var(--orange)"/><rect x="3" y="7" width="6" height="3.5" fill="#fff" stroke="var(--orange)"/></svg>
          +234 1 5550187
        </div>
        <div>
          <svg class="icon" width="12" height="9" viewBox="0 0 12 9" aria-hidden="true"><rect x="0" y="0" width="12" height="9" fill="var(--navy)"/><path d="M0.5 0.5L6 5 11.5 0.5" fill="none" stroke="#fff" stroke-width="1"/></svg>info@halvern.example
          <svg class="icon" width="11" height="11" viewBox="0 0 11 11" aria-hidden="true"><circle cx="5.5" cy="5.5" r="5" fill="var(--navy)"/><path d="M0.5 5.5h10M5.5 0.5v10M5.5 0.5c-3 3-3 7 0 10M5.5 0.5c3 3 3 7 0 10" fill="none" stroke="#fff" stroke-width="0.7"/></svg>
          www.halvern.example
        </div>
      </address>

      <div class="rule-orange"></div>
      <div class="rule-navy"></div>
    </section>

    <section class="page page--cover">
      <div class="cover-top"></div>
      <div class="cover-brand-panel">
        <span class="brand-mark"></span>
        <span class="brand-name"><span class="name">Halvern</span><span class="tag">Property Services</span></span>
      </div>
      <div class="cover-photo" role="img" aria-label="Photograph of a bright modern office lobby with marble columns, a reception desk, glass revolving door and a polished reflective floor"></div>
    </section>

  </div>
</div>
</body>
</html>
```